Business Card Design Project

Business card based on attached logo

Todd Merrick
Todd@lorvantest.com
877-514-9073 ext. 318
Www.LorvanTest.com

Industry/Entity Type

Business

```html
<!DOCTYPE html>
<html lang="en">
<head>
<meta charset="utf-8">
<title>LorvanTest Business Card</title>
<link rel="stylesheet" href="https://fonts.googleapis.com/css2?family=Open+Sans:wght@300;400;600;700&display=swap">
<style>
  :root {
    --stage: #000000;
    --card-grey: #e6e6e6;
    --card-white: #ffffff;
    --brand-red: #ed1c24;
    --brand-black: #231f20;
    --text-grey: #3a3a3a;
  }
  * { margin: 0; padding: 0; box-sizing: border-box; }
  html, body { width: 1200px; height: 1000px; overflow: hidden; background: var(--stage); }
  body { position: relative; font-family: "Open Sans", sans-serif; }

  .card { position: absolute; width: 621px; height: 354px; overflow: hidden; }

  .card-front { left: 50px; top: 62px; background: var(--card-grey); }
  .contact { position: absolute; left: 10px; top: 24px; font-weight: 300; font-size: 16px; line-height: 25px; color: var(--text-grey); }
  .holder { position: absolute; right: 8px; top: 25px; display: flex; align-items: center; gap: 7px; font-weight: 600; font-size: 16px; color: var(--brand-black); }
  .holder-mark { width: 12px; height: 12px; background: var(--brand-red); }
  .band { position: absolute; top: 132px; height: 104px; }
  .band-red { left: 0; width: 311px; background: var(--brand-red); }
  .band-black { left: 311px; right: 0; background: var(--brand-black); }
  .emblem { position: absolute; left: 223px; top: 88px; width: 176px; height: 176px; border-radius: 50%; background: var(--card-white); display: flex; align-items: center; justify-content: center; }
  .brand-name { font-weight: 700; font-size: 26px; color: var(--brand-black); letter-spacing: -0.3px; }

  .card-back { left: 523px; top: 579px; background: var(--card-white); }
  .brand-plate { position: absolute; left: 160px; top: 133px; width: 302px; height: 103px; background: var(--card-grey); box-shadow: 3px 4px 5px rgba(0,0,0,0.45); display: flex; align-items: center; justify-content: center; }
  .brand-plate .brand-name { font-size: 34px; }
  .website { position: absolute; left: 0; right: 0; top: 320px; text-align: center; font-size: 17px; color: var(--brand-black); }
</style>
</head>
<body>
  <section class="card card-front">
    <div class="contact">
      <p>1-877-514-9073 ext 318</p>
      <p>Todd@lorvantest.com</p>
    </div>
    <div class="holder"><span>Todd Merrick</span><span class="holder-mark"></span></div>
    <div class="band band-red"></div>
    <div class="band band-black"></div>
    <div class="emblem"><span class="brand-name">LorvanTest</span></div>
  </section>

  <section class="card card-back">
    <div class="brand-plate"><span class="brand-name">LorvanTest</span></div>
    <p class="website">www.lorvantest.com</p>
  </section>
</body>
</html>
```